Business Card: RW Office Partners - Your organised problem solver

Business Name: RW Office Partners
Website: www.rwofficepartners.com.au
Email: marisol@rwofficepartners.com.au
Mobile: 61 482 907 236
Facebook: @rwofficepartners
Instrgram: @rwofficepartners

Brading Colours:
HEX
#986474
#ddccd3
#7a8498
#c9d8e4
#000000
#ffffff

Tag Line: Your organised problem solver

Link to DRAFT website:
https://deskhelpcollective.wixsite.com/rw-office-partners

About Page from the website:
My name is Marisol Wrenfield, and I would love to assist you to become more productive in your day to day and achieve your business and personal goals.
My mission is to give you time, time to work on the important tasks of your business or to be able to spend more time with your family. I will take on the tasks you don’t have time for, don’t know well or simply don’t like to do.
I have an extensive background in Administration, Tender Coordination, Document Control, WHS and Quality Management working primarily in the Construction, Mining and Corporate World.
I am passionate about being organised, having order and making things in your life (and mine) easier! I love to watch something unfold and grow into something amazing! I am known for being the go-to problem solver, the organiser of all things, producing high standards of work even under pressure. I’m also a confident communicator, and I understand that you’re busy running your business.

Target Market(s)

Small to Medium Business who require assistance in their business by a virtual assistant.

Industry/Entity Type

Virtual Assistant

Contact Information for Business Card

Mobile: 61 482 907 236

Font styles to use
Sans Serif

Colors
ffffff

Requirements
Must have
• Branding Colours as outlined.
Contact Details as outlined.
Logo as provided.
Proper contact details - mobile, facebook, instragm, website.
Simple, Elegant, very clean looking.
Should not have
• Note cute with pictures.
Not too girly as still want to market to construction companies.

```html
<!DOCTYPE html>
<html lang="en">
<head>
<meta charset="utf-8">
<title>RW Office Partners – Business Card</title>
<link href="https://fonts.googleapis.com/css2?family=Montserrat:wght@500&family=Roboto:wght@400;500;700&display=swap" rel="stylesheet">
<style>
  :root {
    --plum: #8a5d6c;
    --plum-brand: #986474;
    --slate: #7a8498;
    --ink: #2b2b2b;
    --paper: #fbfbfb;
    --backdrop: #646061;
  }
  * { box-sizing: border-box; margin: 0; padding: 0; }
  html, body {
    width: 1200px; height: 1200px; overflow: hidden;
    background: var(--backdrop);
    font-family: "Roboto", Arial, sans-serif;
  }
  .canvas { position: relative; width: 1200px; height: 1200px; }

  .card {
    position: absolute;
    background: var(--paper);
    border-radius: 22px;
    overflow: hidden;
  }

  /* Front */
  .card--front { left: 238px; top: 120px; width: 712px; height: 418px; }
  .front__wordmark {
    position: absolute; left: 0; right: 0; top: 150px;
    text-align: center;
    font-family: "Montserrat", Arial, sans-serif;
    font-weight: 500; font-size: 54px; letter-spacing: 1px;
    color: var(--slate);
  }
  .front__social {
    position: absolute; left: 0; right: 0; top: 350px;
    display: flex; justify-content: center; gap: 18px;
    font-size: 18px; color: var(--ink);
  }
  .social-item { display: flex; align-items: center; gap: 10px; }
  .social-mark { width: 16px; height: 16px; border-radius: 3px; background: var(--plum); }
  .front__band { position: absolute; left: 0; right: 0; bottom: 0; height: 18px; display: flex; }
  .front__band-left { width: 356px; background: var(--plum); }
  .front__band-right { flex: 1; background: var(--slate); }

  /* Back */
  .card--back { left: 230px; top: 645px; width: 714px; height: 417px; }
  .back__wordmark {
    position: absolute; left: 45px; top: 62px;
    font-family: "Montserrat", Arial, sans-serif;
    font-weight: 500; font-size: 40px; letter-spacing: 1px;
    color: var(--slate);
  }
  .back__tagline {
    position: absolute; left: 48px; top: 144px;
    font-size: 19px; letter-spacing: 3.2px; color: var(--ink);
  }
  .back__name {
    position: absolute; left: 45px; top: 220px;
    font-size: 26px; font-weight: 700; color: var(--plum);
  }
  .back__role {
    position: absolute; left: 46px; top: 256px;
    font-size: 18px; color: var(--ink);
  }
  .back__waves { position: absolute; inset: 0; }
  .contact-list {
    position: absolute; right: 34px; top: 262px;
    list-style: none;
  }
  .contact-list li {
    display: flex; justify-content: flex-end; align-items: center;
    gap: 14px; height: 26.3px;
    font-size: 18px; color: #fff;
  }
  .contact-icon { width: 17px; height: 17px; flex: none; }
  .contact-mark { width: 15px; height: 15px; border-radius: 3px; background: #fff; flex: none; margin: 0 1px; }
</style>
</head>
<body>
<main class="canvas">

  <section class="card card--front" aria-label="Business card front">
    <div class="front__wordmark">RW Office Partners</div>
    <div class="front__social">
      <span class="social-item"><span class="social-mark"></span>@rwofficepartners</span>
      <span class="social-item"><span class="social-mark"></span>@rwofficepartners</span>
    </div>
    <div class="front__band">
      <div class="front__band-left"></div>
      <div class="front__band-right"></div>
    </div>
  </section>

  <section class="card card--back" aria-label="Business card back">
    <svg class="back__waves" width="714" height="417" viewBox="0 0 714 417" aria-hidden="true">
      <path fill="#7a8498" d="M0 330 C160 380 340 312 470 246 C570 196 650 184 714 186 L714 198 C650 198 572 212 482 257 C352 326 160 400 0 352 Z"/>
      <path fill="#8a5d6c" d="M0 366 C160 405 350 336 485 268 C585 218 650 210 714 210 L714 417 L0 417 Z"/>
    </svg>

    <div class="back__wordmark">RW Office Partners</div>
    <div class="back__tagline">Your organised problem solver</div>
    <div class="back__name">Marisol Wrenfield</div>
    <div class="back__role">Virtual Assistant</div>

    <ul class="contact-list">
      <li>61 482 907 236
        <svg class="contact-icon" viewBox="0 0 24 24" aria-hidden="true"><path fill="#fff" d="M6.6 10.8a15.2 15.2 0 0 0 6.6 6.6l2.2-2.2a1 1 0 0 1 1-.25 11.4 11.4 0 0 0 3.6.57 1 1 0 0 1 1 1V20a1 1 0 0 1-1 1A17 17 0 0 1 3 4a1 1 0 0 1 1-1h3.5a1 1 0 0 1 1 1c0 1.25.2 2.45.57 3.57a1 1 0 0 1-.25 1z"/></svg>
      </li>
      <li>@rwofficepartners <span class="contact-mark"></span></li>
      <li>@rwofficepartners <span class="contact-mark"></span></li>
      <li>www.rwofficepartners.com.au
        <svg class="contact-icon" viewBox="0 0 24 24" aria-hidden="true"><g fill="none" stroke="#fff" stroke-width="1.8"><circle cx="12" cy="12" r="9"/><ellipse cx="12" cy="12" rx="4" ry="9"/><path d="M3 12h18M5 7h14M5 17h14"/></g></svg>
      </li>
      <li>marisol@rwofficepartners.com.au
        <svg class="contact-icon" viewBox="0 0 24 24" aria-hidden="true"><rect x="2.5" y="5" width="19" height="14" rx="1.5" fill="none" stroke="#fff" stroke-width="2"/><path d="M3 6l9 7 9-7" fill="none" stroke="#fff" stroke-width="2"/></svg>
      </li>
    </ul>
  </section>

</main>
</body>
</html>
```